Kestrada LLC, needs a web page no more than 5 pages (for now)

Kestrada is a general contractor. Our services include general contracting, design-build construction, disaster recovery and environmental remediation. Our main clients are PMX, TQ, State and Local Gov't Agencies, Hospitals and Schools. Kestrada is also a SDVOSB.

```html
<!DOCTYPE html>
<html lang="en">
<head>
<meta charset="utf-8">
<title>Kestrada – Home Page, Light and Dark Themes</title>
<link rel="stylesheet" href="https://fonts.googleapis.com/css2?family=Montserrat:wght@400;500;600;700;800&family=Lato:wght@400;700&display=swap">
<style>
:root{
  --canvas:#dcdcdc;
  --gold:#d29a48;
  --gold-light:#e7b766;
  --gold-deep:#a8692a;
  --brown:#7a4620;
  --white:#ffffff;
  --black:#000000;
  --hero-a:#3a2433;
  --hero-b:#5a3322;
  --hero-c:#1c1418;
}
*{margin:0;padding:0;box-sizing:border-box}
html,body{width:1200px;height:2314px;overflow:hidden;background:var(--canvas)}
body{position:relative;font-family:"Lato",sans-serif}

.page{position:absolute;top:30px;width:560px;height:2236px;overflow:hidden;background:var(--page);color:var(--ink)}
.page--light{left:32px;--page:#ffffff;--ink:#111111;--muted:#333333;--band:#fbefe4;--label:#111111;--card:#ffffff;--card-ink:#111111}
.page--dark{left:616px;--page:#000000;--ink:#ffffff;--muted:#ececec;--band:#1a1a1a;--label:#d49a45;--card:#ffffff;--card-ink:#111111}

.abs{position:absolute}
.center{left:0;width:560px;text-align:center}
.heading{font-family:"Montserrat",sans-serif;font-weight:700;text-transform:uppercase;letter-spacing:.5px}
.label{font-family:"Montserrat",sans-serif;font-weight:600;font-size:7.5px;text-transform:uppercase;color:var(--label);letter-spacing:.3px}
.mark{width:14px;height:14px;border-radius:50%;background:linear-gradient(135deg,var(--gold-light),var(--gold-deep))}
.mark--center{left:273px}
.body-copy{font-size:7.4px;line-height:13.5px;color:var(--muted)}

.btn{display:flex;align-items:center;justify-content:center;height:21px;font-family:"Montserrat",sans-serif;font-weight:600;font-size:7px;text-transform:uppercase;letter-spacing:.3px}
.btn--solid{background:linear-gradient(90deg,var(--gold-light),var(--gold-deep));color:var(--white)}
.btn--outline{border:1px solid var(--gold);color:var(--ink)}
.btn--outline-light{border:1px solid var(--gold);color:var(--white)}

/* hero */
.hero{left:0;top:0;width:560px;height:314px;clip-path:polygon(0 0,100% 0,100% 256px,50% 314px,0 256px);
  background:linear-gradient(180deg,var(--hero-c) 0%,var(--hero-a) 30%,var(--hero-b) 70%,#2a1a14 100%)}
.hero-edge{left:0;top:0}
.brand{display:flex;align-items:center;gap:6px;font-family:"Montserrat",sans-serif;font-weight:500;letter-spacing:1px;text-transform:uppercase}
.brand-dot{border-radius:50%;background:var(--gold)}
.brand--header{left:52px;top:22px;font-size:17px;color:var(--white)}
.brand--header .brand-dot{width:14px;height:14px}
.topbar-text{top:8px;font-size:7.5px;color:var(--white)}
.topbar-icon{width:15px;height:15px;border-radius:50%;border:1px solid var(--white);display:flex;align-items:center;justify-content:center}
.topbar-divider{left:418px;top:8px;width:1px;height:11px;background:var(--white)}
.social{top:7px;width:13px;height:13px;border-radius:50%;background:var(--white)}
.social--accent{background:var(--gold)}
.topbar-rule{left:166px;top:30px;width:341px;height:1px;background:rgba(255,255,255,.55)}
.nav{left:166px;top:44px;display:flex;gap:9px;font-family:"Montserrat",sans-serif;font-size:7px;font-weight:500;color:var(--white);text-transform:uppercase}
.nav .is-active{color:var(--gold-light)}
.nav-cta{left:436px;top:40px;width:71px;font-size:6.8px}
.hero-kicker{top:120px;font-family:"Montserrat",sans-serif;font-weight:500;font-size:16.5px;color:var(--white);letter-spacing:.6px}
.hero-title{top:143px;font-size:20px;color:var(--white)}
.hero-copy{top:174px;left:150px;width:260px;text-align:center;font-size:7.4px;line-height:11.5px;color:var(--white)}
.hero-cta{left:237px;top:211px;width:85px}
.slider-dots{left:257px;top:282px;display:flex;gap:5px}
.slider-dots span{width:8px;height:8px;border:1px solid #8a8a8a}
.slider-dots .is-current{background:var(--gold);border-color:var(--gold)}

/* photo placeholders */
.photo{background:linear-gradient(135deg,#6d7884,#3b3f48 55%,#a66f3b)}
.frame{border:2px solid var(--brown)}

/* about */
.about-frame{left:51px;top:351px;width:222px;height:243px}
.about-photo{left:57px;top:357px;width:216px;height:231px;background:linear-gradient(135deg,#9aa3ad 0%,#e0a43a 30%,#394553 60%,#7d7a72 100%)}
.about-mark{left:297px;top:362px}
.about-label{left:297px;top:381px}
.about-title{left:297px;top:396px;font-size:19px}
.about-copy{left:297px;top:428px;width:222px}
.about-copy p+p{margin-top:13.5px}
.about-cta{left:297px;top:561px;width:84px}

/* services */
.services-band{left:0;top:657px;width:560px;height:337px;background:var(--band)}
.services-watermark{top:660px;font-family:"Montserrat",sans-serif;font-weight:800;font-size:60px;color:#2c2c2c;letter-spacing:1px;line-height:60px}
.services-mark{top:692px}
.services-label{top:715px}
.services-title{top:730px;font-size:19px}
.card{top:768px;width:109px;height:145px;background:var(--card);color:var(--card-ink)}
.card--open{height:177px;box-shadow:0 2px 6px rgba(0,0,0,.18)}
.card-photo{left:0;top:0;width:109px;height:98px;clip-path:polygon(0 0,100% 0,100% 100%,50% 88%,0 100%)}
.card-title{left:0;top:104px;width:109px;text-align:center;font-family:"Montserrat",sans-serif;font-weight:700;font-size:7.3px;line-height:12px;text-transform:uppercase}
.card-copy{left:8px;top:136px;width:93px;text-align:center;font-size:5.6px;line-height:8.3px;color:#444}
.card-arrow{left:46px;top:137px;width:17px;height:17px;border-radius:50%;background:var(--brown);display:flex;align-items:center;justify-content:center}
.card--open .card-arrow{top:169px}

/* projects */
.projects-mark{top:1044px}
.projects-label{top:1067px}
.projects-title{top:1082px;font-size:19px}
.tile{height:113px}
.tile--brand{background:linear-gradient(135deg,#b9773a,#8f5522)}
.projects-cta{left:227px;top:1384px;width:105px}

/* certification */
.cert-band{left:0;top:1443px;width:560px;height:220px;background:linear-gradient(180deg,#241d30 0%,#2e2536 55%,#3a2a20 100%)}
.cert-mark{top:1480px}
.cert-label{top:1506px;color:var(--white)}
.cert-title{top:1523px;font-size:19.5px;line-height:24px;color:var(--white);font-weight:800}
.cert-cta{left:227px;top:1587px;width:105px}

/* client focus */
.client-mark{left:51px;top:1722px}
.client-label{left:51px;top:1748px}
.client-title{left:51px;top:1765px;font-size:18.5px;line-height:24px;font-weight:800}
.client-copy{left:51px;top:1874px;width:210px}
.client-cta{left:51px;top:1929px;width:84px}
.client-frame{left:286px;top:1713px;width:222px;height:242px}
.client-photo{left:286px;top:1719px;width:218px;height:231px;background:linear-gradient(135deg,#8a96a6 0%,#c9cdb2 35%,#4f6f9c 65%,#b47a3c 100%)}

/* footer */
.footer{left:0;top:2016px;width:560px;height:220px;background:var(--black);clip-path:polygon(50% 0,100% 58px,100% 100%,0 100%,0 58px)}
.page--dark .footer{clip-path:none}
.brand--footer{left:54px;top:2130px;font-size:28px;color:var(--white)}
.brand--footer .brand-dot{width:22px;height:22px}
.footer-heading{top:2082px;font-family:"Montserrat",sans-serif;font-weight:500;font-size:11px;color:var(--white);text-transform:uppercase}
.footer-links{left:255px;top:2101px;list-style:none;font-size:7px;color:var(--white)}
.footer-links li{height:16px;display:flex;align-items:center;gap:6px}
.footer-links li::before{content:"»";color:var(--gold);font-size:9px}
.contact-item{left:381px;display:flex;gap:8px;font-size:7px;line-height:10px;color:var(--white)}
.copyright{top:2210px;font-size:7px;color:var(--white)}
</style>
</head>
<body>

<!-- ============ LIGHT THEME ============ -->
<main class="page page--light">
  <div class="abs hero" role="img" aria-label="Dusk photo of a modern institutional building with light trails"></div>

  <div class="abs brand brand--header"><span class="brand-dot"></span>Kestrada</div>
  <div class="abs topbar-text" style="left:234px">Talk to us Today</div>
  <div class="abs topbar-icon" style="left:319px;top:6px"><svg width="8" height="8" viewBox="0 0 24 24"><path fill="#fff" d="M6.6 10.8a15 15 0 0 0 6.6 6.6l2.2-2.2c.3-.3.7-.4 1-.2 1.1.4 2.3.6 3.6.6.6 0 1 .4 1 1V20c0 .6-.4 1-1 1A17 17 0 0 1 3 4c0-.6.4-1 1-1h3.5c.6 0 1 .4 1 1 0 1.3.2 2.5.6 3.6.1.3 0 .7-.2 1z"/></svg></div>
  <div class="abs topbar-text" style="left:338px">+1 555-201-4400</div>
  <div class="abs topbar-divider"></div>
  <div class="abs social social--accent" style="left:438px"></div>
  <div class="abs social" style="left:457px"></div>
  <div class="abs social" style="left:476px"></div>
  <div class="abs social" style="left:495px"></div>
  <div class="abs topbar-rule"></div>
  <nav class="abs nav"><span class="is-active">Home</span><span>|</span><span>About Us</span><span>|</span><span>Services</span><span>|</span><span>Projects</span><span>|</span><span>Contact</span></nav>
  <div class="abs btn btn--solid nav-cta">Request Info</div>

  <div class="abs center hero-kicker">BUILDING WITH INTEGRITY</div>
  <div class="abs center heading hero-title">Restoring With Purpose</div>
  <p class="abs hero-copy">Trusted partner in construction, disaster recovery, and remediation for government and institutional clients.</p>
  <div class="abs btn btn--solid hero-cta">Get Started</div>
  <div class="abs slider-dots"><span></span><span class="is-current"></span><span></span><span></span></div>

  <div class="abs frame about-frame"></div>
  <div class="abs about-photo" role="img" aria-label="Contractor in a hard hat reviewing plans on a tablet"></div>
  <div class="abs mark about-mark"></div>
  <div class="abs label about-label">About Us</div>
  <h2 class="abs heading about-title">Who We Are</h2>
  <div class="abs body-copy about-copy">
    <p>Kestrada is a trusted general contractor dedicated to serving federal, state, and local government agencies, hospitals, and schools. With a commitment to integrity, quality, and safety, we deliver construction and recovery solutions that keep critical infrastructure running.</p>
    <p>As a Service-Disabled Veteran-Owned Small Business (SDVOSB), we bring military precision, discipline, and accountability to every project we take on.</p>
  </div>
  <div class="abs btn btn--solid about-cta">Read More</div>

  <div class="abs services-band"></div>
  <div class="abs mark mark--center services-mark"></div>
  <div class="abs center label services-label">What We Do</div>
  <h2 class="abs center heading services-title">Our Services</h2>
  <div class="abs card" style="left:52px"><div class="abs card-photo photo" role="img" aria-label="Site manager checking a phone on a job site"></div><div class="abs card-title">General<br>Contracting</div><div class="abs card-arrow"><svg width="7" height="7" viewBox="0 0 10 10"><path d="M3 1l4 4-4 4" stroke="#fff" stroke-width="1.8" fill="none"/></svg></div></div>
  <div class="abs card card--open" style="left:167px"><div class="abs card-photo photo" role="img" aria-label="Hand sketching architectural plans"></div><div class="abs card-title">Design-Build<br>Construction</div><p class="abs card-copy">A single point of responsibility for planning, design, and construction, reducing risk and</p><div class="abs card-arrow"><svg width="7" height="7" viewBox="0 0 10 10"><path d="M3 1l4 4-4 4" stroke="#fff" stroke-width="1.8" fill="none"/></svg></div></div>
  <div class="abs card" style="left:283px"><div class="abs card-photo photo" role="img" aria-label="Team meeting in a coordination room"></div><div class="abs card-title">Disaster<br>Recovery</div><div class="abs card-arrow"><svg width="7" height="7" viewBox="0 0 10 10"><path d="M3 1l4 4-4 4" stroke="#fff" stroke-width="1.8" fill="none"/></svg></div></div>
  <div class="abs card" style="left:399px"><div class="abs card-photo photo" role="img" aria-label="Workers in safety gear sampling soil by water"></div><div class="abs card-title">Environmental<br>Remediation</div><div class="abs card-arrow"><svg width="7" height="7" viewBox="0 0 10 10"><path d="M3 1l4 4-4 4" stroke="#fff" stroke-width="1.8" fill="none"/></svg></div></div>

  <div class="abs mark mark--center projects-mark"></div>
  <div class="abs center label projects-label">Projects</div>
  <h2 class="abs center heading projects-title">Past Projects</h2>
  <div class="abs tile photo" style="left:52px;top:1125px;width:161px" role="img" aria-label="Glass atrium interior with people walking"></div>
  <div class="abs tile tile--brand" style="left:224px;top:1125px;width:162px" role="img" aria-label="Historic building facade under a bronze overlay"></div>
  <div class="abs tile photo" style="left:396px;top:1125px;width:112px" role="img" aria-label="Workers in orange shirts on a construction site"></div>
  <div class="abs tile photo" style="left:52px;top:1248px;width:112px" role="img" aria-label="Stone columns against a blue sky"></div>
  <div class="abs tile photo" style="left:174px;top:1248px;width:162px" role="img" aria-label="Capitol dome at sunset"></div>
  <div class="abs tile photo" style="left:346px;top:1248px;width:162px" role="img" aria-label="Modern hospital campus building"></div>
  <div class="abs btn btn--outline projects-cta">View All Projects</div>

  <div class="abs cert-band" role="img" aria-label="Night view of a city street lined with government buildings"></div>
  <div class="abs mark mark--center cert-mark"></div>
  <div class="abs center label cert-label">SDVOSB Certification</div>
  <h2 class="abs center heading cert-title">Proudly Certified as a Service-Disabled<br>Veteran-Owned Small Business.</h2>
  <div class="abs btn btn--outline-light cert-cta">View All</div>

  <div class="abs mark client-mark"></div>
  <div class="abs label client-label">Client Focus</div>
  <h2 class="abs heading client-title">Serving PMX, TQ,<br>State &amp; Local Gov’t,<br>Hospitals, and<br>Schools</h2>
  <p class="abs body-copy client-copy">As a Service-Disabled Veteran-Owned Small Business (SDVOSB), we bring military precision, discipline, and accountability to every project we take on.</p>
  <div class="abs btn btn--solid client-cta">Read More</div>
  <div class="abs frame client-frame"></div>
  <div class="abs client-photo" role="img" aria-label="Contractor and client shaking hands at a building site"></div>

  <footer class="abs footer"></footer>
  <div class="abs brand brand--footer"><span class="brand-dot"></span>Kestrada</div>
  <div class="abs footer-heading" style="left:255px">Quick Links</div>
  <ul class="abs footer-links"><li>Home</li><li>About</li><li>Services</li><li>Projects</li><li>Contact</li></ul>
  <div class="abs footer-heading" style="left:381px">Contact Info</div>
  <div class="abs contact-item" style="top:2101px"><svg width="8" height="9" viewBox="0 0 24 24"><path fill="#d29a48" d="M12 2a7 7 0 0 0-7 7c0 5 7 13 7 13s7-8 7-13a7 7 0 0 0-7-7zm0 9.5A2.5 2.5 0 1 1 12 6.5a2.5 2.5 0 0 1 0 5z"/></svg><span>1180 Harlow Ridge Suite<br>310</span></div>
  <div class="abs contact-item" style="top:2136px"><svg width="8" height="8" viewBox="0 0 24 24"><path fill="#d29a48" d="M6.6 10.8a15 15 0 0 0 6.6 6.6l2.2-2.2c.3-.3.7-.4 1-.2 1.1.4 2.3.6 3.6.6.6 0 1 .4 1 1V20c0 .6-.4 1-1 1A17 17 0 0 1 3 4c0-.6.4-1 1-1h3.5c.6 0 1 .4 1 1 0 1.3.2 2.5.6 3.6.1.3 0 .7-.2 1z"/></svg><span>+1 (555)-201-4400</span></div>
  <div class="abs contact-item" style="top:2164px"><svg width="8" height="8" viewBox="0 0 24 24"><path fill="#d29a48" d="M2 5h20v14H2zm2 2v.5l8 5 8-5V7z"/></svg><span>info@kestrada.com</span></div>
  <div class="abs center copyright">Copyright 2025. Kestrada. All Rights Reserved</div>
</main>

<!-- ============ DARK THEME ============ -->
<main class="page page--dark">
  <div class="abs hero" role="img" aria-label="Dusk photo of a modern institutional building with light trails"></div>
  <svg class="abs hero-edge" width="560" height="320"><polyline points="0,256 280,314 560,256" fill="none" stroke="#c08a3e" stroke-width="2"/></svg>

  <div class="abs brand brand--header"><span class="brand-dot"></span>Kestrada</div>
  <div class="abs topbar-text" style="left:234px">Talk to us Today</div>
  <div class="abs topbar-icon" style="left:319px;top:6px"><svg width="8" height="8" viewBox="0 0 24 24"><path fill="#fff" d="M6.6 10.8a15 15 0 0 0 6.6 6.6l2.2-2.2c.3-.3.7-.4 1-.2 1.1.4 2.3.6 3.6.6.6 0 1 .4 1 1V20c0 .6-.4 1-1 1A17 17 0 0 1 3 4c0-.6.4-1 1-1h3.5c.6 0 1 .4 1 1 0 1.3.2 2.5.6 3.6.1.3 0 .7-.2 1z"/></svg></div>
  <div class="abs topbar-text" style="left:338px">+1 555-201-4400</div>
  <div class="abs topbar-divider"></div>
  <div class="abs social social--accent" style="left:438px"></div>
  <div class="abs social" style="left:457px"></div>
  <div class="abs social" style="left:476px"></div>
  <div class="abs social" style="left:495px"></div>
  <div class="abs topbar-rule"></div>
  <nav class="abs nav"><span class="is-active">Home</span><span>|</span><span>About Us</span><span>|</span><span>Services</span><span>|</span><span>Projects</span><span>|</span><span>Contact</span></nav>
  <div class="abs btn btn--solid nav-cta">Request Info</div>

  <div class="abs center hero-kicker">BUILDING WITH INTEGRITY</div>
  <div class="abs center heading hero-title">Restoring With Purpose</div>
  <p class="abs hero-copy">Trusted partner in construction, disaster recovery, and remediation for government and institutional clients.</p>
  <div class="abs btn btn--solid hero-cta">Get Started</div>
  <div class="abs slider-dots"><span></span><span class="is-current"></span><span></span><span></span></div>

  <div class="abs frame about-frame"></div>
  <div class="abs about-photo" role="img" aria-label="Contractor in a hard hat reviewing plans on a tablet"></div>
  <div class="abs mark about-mark"></div>
  <div class="abs label about-label">About Us</div>
  <h2 class="abs heading about-title">Who We Are</h2>
  <div class="abs body-copy about-copy">
    <p>Kestrada is a trusted general contractor dedicated to serving federal, state, and local government agencies, hospitals, and schools. With a commitment to integrity, quality, and safety, we deliver construction and recovery solutions that keep critical infrastructure running.</p>
    <p>As a Service-Disabled Veteran-Owned Small Business (SDVOSB), we bring military precision, discipline, and accountability to every project we take on.</p>
  </div>
  <div class="abs btn btn--solid about-cta">Read More</div>

  <div class="abs services-band"></div>
  <div class="abs center services-watermark">OUR SERVICES</div>
  <div class="abs mark mark--center services-mark"></div>
  <div class="abs center label services-label">What We Do</div>
  <h2 class="abs center heading services-title">Our Services</h2>
  <div class="abs card" style="left:52px"><div class="abs card-photo photo" role="img" aria-label="Site manager checking a phone on a job site"></div><div class="abs card-title">General<br>Contracting</div><div class="abs card-arrow"><svg width="7" height="7" viewBox="0 0 10 10"><path d="M3 1l4 4-4 4" stroke="#fff" stroke-width="1.8" fill="none"/></svg></div></div>
  <div class="abs card card--open" style="left:167px"><div class="abs card-photo photo" role="img" aria-label="Hand sketching architectural plans"></div><div class="abs card-title">Design-Build<br>Construction</div><p class="abs card-copy">A single point of responsibility for planning, design, and construction, reducing risk and</p><div class="abs card-arrow"><svg width="7" height="7" viewBox="0 0 10 10"><path d="M3 1l4 4-4 4" stroke="#fff" stroke-width="1.8" fill="none"/></svg></div></div>
  <div class="abs card" style="left:283px"><div class="abs card-photo photo" role="img" aria-label="Team meeting in a coordination room"></div><div class="abs card-title">Disaster<br>Recovery</div><div class="abs card-arrow"><svg width="7" height="7" viewBox="0 0 10 10"><path d="M3 1l4 4-4 4" stroke="#fff" stroke-width="1.8" fill="none"/></svg></div></div>
  <div class="abs card" style="left:399px"><div class="abs card-photo photo" role="img" aria-label="Workers in safety gear sampling soil by water"></div><div class="abs card-title">Environmental<br>Remediation</div><div class="abs card-arrow"><svg width="7" height="7" viewBox="0 0 10 10"><path d="M3 1l4 4-4 4" stroke="#fff" stroke-width="1.8" fill="none"/></svg></div></div>

  <div class="abs mark mark--center projects-mark"></div>
  <div class="abs center label projects-label">Projects</div>
  <h2 class="abs center heading projects-title">Past Projects</h2>
  <div class="abs tile photo" style="left:52px;top:1125px;width:161px" role="img" aria-label="Glass atrium interior with people walking"></div>
  <div class="abs tile tile--brand" style="left:224px;top:1125px;width:162px" role="img" aria-label="Historic building facade under a bronze overlay"></div>
  <div class="abs tile photo" style="left:396px;top:1125px;width:112px" role="img" aria-label="Workers in orange shirts on a construction site"></div>
  <div class="abs tile photo" style="left:52px;top:1248px;width:112px" role="img" aria-label="Stone columns against a blue sky"></div>
  <div class="abs tile photo" style="left:174px;top:1248px;width:162px" role="img" aria-label="Capitol dome at sunset"></div>
  <div class="abs tile photo" style="left:346px;top:1248px;width:162px" role="img" aria-label="Modern hospital campus building"></div>
  <div class="abs btn btn--outline projects-cta">View All Projects</div>

  <div class="abs cert-band" role="img" aria-label="Night view of a city street lined with government buildings"></div>
  <div class="abs mark mark--center cert-mark"></div>
  <div class="abs center label cert-label">SDVOSB Certification</div>
  <h2 class="abs center heading cert-title">Proudly Certified as a Service-Disabled<br>Veteran-Owned Small Business.</h2>
  <div class="abs btn btn--outline-light cert-cta">View All</div>

  <div class="abs mark client-mark"></div>
  <div class="abs label client-label">Client Focus</div>
  <h2 class="abs heading client-title">Serving PMX, TQ,<br>State &amp; Local Gov’t,<br>Hospitals, and<br>Schools</h2>
  <p class="abs body-copy client-copy">As a Service-Disabled Veteran-Owned Small Business (SDVOSB), we bring military precision, discipline, and accountability to every project we take on.</p>
  <div class="abs btn btn--solid client-cta">Read More</div>
  <div class="abs frame client-frame"></div>
  <div class="abs client-photo" role="img" aria-label="Contractor and client shaking hands at a building site"></div>

  <footer class="abs footer"></footer>
  <svg class="abs" style="left:0;top:2010px" width="560" height="70"><polyline points="44,64 280,6 516,64" fill="none" stroke="#a8692a" stroke-width="2"/></svg>
  <div class="abs brand brand--footer"><span class="brand-dot"></span>Kestrada</div>
  <div class="abs footer-heading" style="left:255px">Quick Links</div>
  <ul class="abs footer-links"><li>Home</li><li>About</li><li>Services</li><li>Projects</li><li>Contact</li></ul>
  <div class="abs footer-heading" style="left:381px">Contact Info</div>
  <div class="abs contact-item" style="top:2101px"><svg width="8" height="9" viewBox="0 0 24 24"><path fill="#d29a48" d="M12 2a7 7 0 0 0-7 7c0 5 7 13 7 13s7-8 7-13a7 7 0 0 0-7-7zm0 9.5A2.5 2.5 0 1 1 12 6.5a2.5 2.5 0 0 1 0 5z"/></svg><span>1180 Harlow Ridge Suite<br>310</span></div>
  <div class="abs contact-item" style="top:2136px"><svg width="8" height="8" viewBox="0 0 24 24"><path fill="#d29a48" d="M6.6 10.8a15 15 0 0 0 6.6 6.6l2.2-2.2c.3-.3.7-.4 1-.2 1.1.4 2.3.6 3.6.6.6 0 1 .4 1 1V20c0 .6-.4 1-1 1A17 17 0 0 1 3 4c0-.6.4-1 1-1h3.5c.6 0 1 .4 1 1 0 1.3.2 2.5.6 3.6.1.3 0 .7-.2 1z"/></svg><span>+1 (555)-201-4400</span></div>
  <div class="abs contact-item" style="top:2164px"><svg width="8" height="8" viewBox="0 0 24 24"><path fill="#d29a48" d="M2 5h20v14H2zm2 2v.5l8 5 8-5V7z"/></svg><span>info@kestrada.com</span></div>
  <div class="abs center copyright">Copyright 2025. Kestrada. All Rights Reserved</div>
</main>

</body>
</html>
```